Dog grooming business card
This is a business card for m dog grooming business like it say above.
In the priorities box below I will have the text that I want on the card.

Industry/Entity Type

Business

Colors

Designer to choose colors to be used in the design.

Requirements
Must have
• My logo and the insurance stamp must be on the card.

Text it must have :

Professional grooming services
Email: lunabrisk@mailvale.net
Text or call 1 705 318 6052
TWF certified/member
Pet first aid certified
Next appointment ___________________________________
Nice to have
• Greens to match my logo

```html
<!DOCTYPE html>
<html lang="en">
<head>
<meta charset="utf-8">
<title>Luna Brisk – Business Card</title>
<link rel="stylesheet" href="https://fonts.googleapis.com/css2?family=Arimo:wght@400;700&family=Lobster&display=swap">
<style>
  :root {
    --page: #e9e6e2;
    --card-white: #ffffff;
    --card-black: #231f20;
    --green: #9cc63f;
    --green-text: #8dbb2f;
    --ink: #222222;
    --faint: #3a3637;
    --badge-line: #5b86c5;
    --badge-fill: #eef3fb;
  }
  * { box-sizing: border-box; margin: 0; padding: 0; }
  html, body {
    width: 1200px; height: 914px; overflow: hidden;
    background: var(--page);
    font-family: "Arimo", Arial, sans-serif;
    color: var(--ink);
  }
  .sheet {
    position: relative; width: 1200px; height: 914px;
    display: flex; flex-direction: column; align-items: center; justify-content: center; gap: 40px;
  }
  .card {
    position: relative; width: 700px; height: 400px; overflow: hidden;
    box-shadow: 0 6px 18px rgba(0,0,0,.18);
  }

  /* Front */
  .card--front { background: var(--card-white); }
  .appointment-label {
    position: absolute; left: 44px; top: 38px;
    color: var(--green-text); font-size: 16px;
  }
  .appointment-line {
    position: absolute; left: 44px; top: 80px; width: 380px;
    border-top: 2px dotted var(--ink);
  }
  .credentials { position: absolute; left: 44px; top: 100px; }
  .credential--primary { font-weight: 700; font-size: 20px; }
  .credential--secondary { font-weight: 700; font-size: 16px; margin-top: 6px; }
  .insurance-badge {
    position: absolute; left: 44px; top: 164px; width: 112px; height: 46px;
    border: 2px solid var(--badge-line); border-radius: 8px; background: var(--badge-fill);
  }
  .contact { position: absolute; left: 44px; top: 222px; font-size: 15px; }
  .contact-line + .contact-line { margin-top: 6px; }
  .contact .accent { color: var(--green-text); font-weight: 700; }

  .brand {
    position: absolute; right: 46px; top: 150px;
    display: flex; align-items: center; gap: 10px;
  }
  .brand-dot { width: 26px; height: 26px; border-radius: 50%; background: var(--green); }
  .brand-name { font-size: 30px; font-weight: 700; color: var(--green-text); }

  .services-band {
    position: absolute; left: 0; right: 0; bottom: 0; height: 120px;
    background: var(--green);
    display: flex; align-items: center; padding-left: 44px;
  }
  .services-title {
    font-family: "Lobster", cursive; font-size: 50px; color: var(--ink);
  }

  /* Back */
  .card--back { background: var(--card-black); }
  .back-mark {
    position: absolute; left: 60px; top: 30px; width: 230px; height: 230px;
    border-radius: 50%; background: var(--faint);
  }
  .back-brand {
    position: absolute; right: 50px; bottom: 60px;
    display: flex; align-items: center; gap: 10px;
  }
  .back-brand .brand-name { font-size: 32px; }
</style>
</head>
<body>
<main class="sheet">
  <section class="card card--front" aria-label="Card front">
    <p class="appointment-label">Next appointment</p>
    <div class="appointment-line"></div>
    <div class="credentials">
      <p class="credential--primary">Pet first aid certified</p>
      <p class="credential--secondary">TWF certified/member</p>
    </div>
    <div class="insurance-badge" role="img" aria-label="Insurance protection stamp"></div>
    <div class="contact">
      <p class="contact-line">lunabrisk@mailvale.net</p>
      <p class="contact-line"><span class="accent">Text</span> or <span class="accent">call</span> 1 705 318 6052</p>
    </div>
    <div class="brand">
      <span class="brand-dot"></span>
      <span class="brand-name">Luna Brisk</span>
    </div>
    <div class="services-band">
      <h1 class="services-title">Professional grooming services</h1>
    </div>
  </section>

  <section class="card card--back" aria-label="Card back">
    <div class="back-mark"></div>
    <div class="back-brand">
      <span class="brand-dot"></span>
      <span class="brand-name">Luna Brisk</span>
    </div>
  </section>
</main>
</body>
</html>
```